Hollendorf Business Card

This is the personal business card for Dr Mark Hollendorf and convers three area of his professional activity - all of them involve (foreign) languages:
o QRVB International Ltd - A translation company with 50 staff. Trades internationally
o WideHarbor Ltd - a global online auction marketplace for translation services (startup)
o Tonal Mosaic - cutting edge technology from the brain sciences which helps learners assimilate the sound patterns of a new language (startup)

Target Market(s)

The card needs to have a "cutting edge" feel - but for a fairly conservative audience - academics, investors.

Industry/Entity Type

Business

Requirements
Must have
• Text:
Dr Mark Hollendorf

Co-founder QRVB International Ltd (Language translation)
Founder WideHarbor Ltd (Translation marketplace)
Founder Tonal Mosaic (Language acquisition)

email: mark.oswin@velmora.co.nz
Phone: +64 21 596 3172
Twitter: @MarkOswin7

```html
<!DOCTYPE html>
<html lang="en">
<head>
<meta charset="utf-8">
<title>Dr. Mark Hollendorf – Business Card</title>
<link href="https://fonts.googleapis.com/css2?family=Oswald:wght@300;400;500&family=Roboto+Condensed:wght@300;700&display=swap" rel="stylesheet">
<style>
  :root {
    --paper: #ffffff;
    --ink: #111111;
    --band: #cfe9e8;
    --accent: #d7e84a;
  }
  * { margin: 0; padding: 0; box-sizing: border-box; }
  html, body { width: 1200px; height: 686px; overflow: hidden; background: var(--paper); }
  .card {
    position: relative;
    width: 1200px;
    height: 686px;
    background: var(--paper);
    color: var(--ink);
    overflow: hidden;
  }
  .top-band {
    position: absolute;
    left: 302px; top: 0;
    width: 898px; height: 114px;
    background: var(--band);
  }
  .card-title {
    position: absolute;
    left: 171px; top: 72px;
    font-family: "Oswald", sans-serif;
    font-weight: 400;
    font-size: 56px;
    line-height: 1;
    letter-spacing: 0.5px;
    transform: scaleX(0.86);
    transform-origin: left top;
  }
  .side-name, .side-tagline {
    position: absolute;
    writing-mode: vertical-rl;
    transform: rotate(180deg);
    white-space: nowrap;
    line-height: 1;
  }
  .side-name {
    left: 164px; top: 228px;
    font-family: "Oswald", sans-serif;
    font-weight: 500;
    font-size: 54px;
    letter-spacing: 1px;
  }
  .side-tagline {
    left: 242px; top: 222px;
    font-family: "Roboto Condensed", sans-serif;
    font-weight: 700;
    font-size: 24px;
  }
  .accent-rule {
    position: absolute;
    left: 227px; top: 340px;
    width: 6px; height: 324px;
  }
  .ventures {
    position: absolute;
    left: 345px; top: 348px;
    list-style: none;
    font-family: "Roboto Condensed", sans-serif;
    font-weight: 300;
    font-size: 24px;
    line-height: 37px;
  }
  .ventures li + li { margin-top: 20px; }
  .contact {
    position: absolute;
    left: 775px; top: 346px;
    font-family: "Roboto Condensed", sans-serif;
    font-weight: 700;
    font-size: 28px;
    line-height: 41px;
  }
  .contact p { white-space: nowrap; }
</style>
</head>
<body>
  <main class="card">
    <div class="top-band"></div>
    <h1 class="card-title">Dr. Mark Hollendorf</h1>

    <div class="side-name">Mark Hollendorf</div>
    <div class="side-tagline">Profession in Foreign Languages</div>
    <svg class="accent-rule" viewBox="0 0 6 324" aria-hidden="true">
      <line x1="3" y1="0" x2="3" y2="324" stroke="var(--accent)" stroke-width="4" stroke-dasharray="14 10"/>
    </svg>

    <ul class="ventures">
      <li>Co-founder QRVB International<br>Ltd (Language Translation)</li>
      <li>Founder WideHarbor Ltd<br>(Translation Marketplace)</li>
      <li>Founder Tonal Mosaic (Language<br>Acquisition)</li>
    </ul>

    <div class="contact">
      <p>Phone: +64 21 596 3172</p>
      <p>Twitter: @MarkOswin7</p>
      <p>E-mail:</p>
      <p>mark.oswin@velmora.co.nz</p>
    </div>
  </main>
</body>
</html>
```